letter flyer KORVEN

please see our website www.tallowcrestpartners.com.au for details. however, we are a financial services company that has services in accounting and taxation, wealth advice, loan broking, general insurance and business advice. we want to target local potential business clients to focus on helping them conduct a review and work out what they need to do to improve the health and profitability of their business. we would like to create a letter/flyer to send them. we want the message to be as follows:
1) by having a review, we guarantee we will provide some financial benefit;
2) we are offering a cohesive and comprehensive team who will provide many financial services under one roof; and
3) we specialise in business.

we have called the campaign 'KORVEN'

we have drafted a letter as a concept and we need design, any suggested changes in wording and imagery to demonstrate our message. We do have a logo for each of the divisions above. we thought the reverse side could just be our logo and catchphrase 'financial freedom is...'

***** we just want an A4 letter... not a bifold flyer
***** I have also included a copy of our newsletter so you can get the logos and feel for our business

```html
<!DOCTYPE html>
<html lang="en">
<head>
<meta charset="utf-8">
<title>KORVEN – Tallowcrest Partners Letter</title>
<link href="https://fonts.googleapis.com/css2?family=Lato:wght@400;700&family=Montserrat:wght@800&family=Roboto+Condensed:wght@700&display=swap" rel="stylesheet">
<style>
:root{
  --orange:#f07d1a;
  --orange-light:#f7a23c;
  --blue:#1e8fe0;
  --blue-dark:#1467bd;
  --ink:#2b2b2b;
  --white:#ffffff;
  --stage:#e6e7e9;
  --gold:#d98a1e;
}
*{margin:0;padding:0;box-sizing:border-box}
html,body{width:806px;height:1200px;overflow:hidden;background:var(--stage)}
.flyer{position:absolute;left:0;top:33px;width:806px;height:1133px;background:var(--white);overflow:hidden;font-family:'Lato',sans-serif;color:var(--ink)}
.shapes{position:absolute;left:0;top:0}
.photo{position:absolute;left:428px;top:171px;width:396px;height:396px;border-radius:50%;
  background:radial-gradient(circle at 38% 55%,#f1f3f5 0%,#cfd8e2 35%,#5c6f8c 70%,#26344d 100%)}
.brand{position:absolute;left:30px;top:30px;display:flex;align-items:center;gap:10px}
.brand-dot{width:64px;height:64px;border-radius:50%;background:var(--blue-dark)}
.brand-name{font-family:'Lato',sans-serif;font-weight:700;font-size:20px;line-height:22px;color:var(--blue-dark);width:160px}
.brand-tag{position:absolute;left:30px;top:120px;font-weight:700;font-size:12.5px;color:var(--gold);letter-spacing:.3px}
.divider{position:absolute;left:253px;top:24px;width:2px;height:90px;background:#d4d4d4}
.call{position:absolute;left:274px;top:40px}
.call-line{font-weight:700;font-size:20px;color:var(--blue)}
.call-quote{font-size:27px;color:var(--ink);margin-top:2px}
.headline{position:absolute;left:20px;top:192px;font-family:'Roboto Condensed',sans-serif;font-weight:700;font-size:50px;color:var(--ink);letter-spacing:-.5px}
.subline{position:absolute;left:22px;top:248px;font-family:'Roboto Condensed',sans-serif;font-weight:700;font-size:18.5px;line-height:36px;color:var(--white);letter-spacing:.3px}
.questions{position:absolute;left:28px;top:352px;list-style:none}
.questions li{display:flex;align-items:flex-start;gap:16px;height:66px;font-weight:700;font-size:15px;line-height:19px;color:var(--white)}
.q-icon{flex:none;width:26px;height:26px;border-radius:50%;background:var(--blue);border:2px solid var(--white)}
.pill{position:absolute;left:0;height:29px;border-radius:0 15px 15px 0;background:var(--blue);color:var(--white);font-family:'Roboto Condensed',sans-serif;font-weight:700;font-size:19px;line-height:29px;padding-left:20px}
.pill-about{top:590px;width:120px}
.pill-special{top:794px;width:178px}
.about-text{position:absolute;left:20px;top:642px;width:440px;font-size:15px;line-height:19px;text-align:justify;color:var(--ink)}
.special-list{position:absolute;left:26px;top:850px;width:440px;list-style:none;font-weight:700;font-size:15px;line-height:23.5px}
.special-list li{position:relative;padding-left:18px}
.special-list li::before{content:"";position:absolute;left:0;top:8px;width:7px;height:7px;border-radius:50%;background:var(--blue)}
.cta{position:absolute;left:20px;top:988px}
.cta-title{font-family:'Montserrat',sans-serif;font-weight:800;font-size:23px;color:var(--blue);letter-spacing:.3px}
.cta-sub{font-family:'Roboto Condensed',sans-serif;font-weight:700;font-size:14.5px;color:var(--ink);margin-top:2px;letter-spacing:.2px}
.contact{position:absolute;left:20px;top:1082px;font-weight:700;font-size:14px;color:var(--white)}
.contact-row{display:flex;gap:64px;height:22px;align-items:center}
.contact-item{display:flex;align-items:center;gap:6px}
.meaning{position:absolute;left:530px;top:725px;width:262px}
.meaning-title{font-family:'Roboto Condensed',sans-serif;font-weight:700;font-size:32px;line-height:34px;color:var(--ink)}
.meaning-sub{font-family:'Lato',sans-serif;font-weight:700;font-size:26px;line-height:34px;color:var(--white);padding-bottom:8px;border-bottom:2px solid var(--white)}
.meaning-list{list-style:none;margin-top:18px;font-weight:700;font-size:15px;line-height:19.5px;color:var(--white);text-align:justify}
.meaning-list li{position:relative;padding-left:18px;padding-right:8px;margin-bottom:38px}
.meaning-list li::before{content:"";position:absolute;left:2px;top:7px;width:6px;height:6px;border-radius:50%;background:var(--white)}
</style>
</head>
<body>
<main class="flyer">
  <svg class="shapes" width="806" height="1133" viewBox="0 0 806 1133" aria-hidden="true">
    <defs>
      <linearGradient id="bannerFill" x1="0" y1="0" x2="1" y2="1">
        <stop offset="0" stop-color="#f59a2c"/>
        <stop offset="1" stop-color="#ee7414"/>
      </linearGradient>
      <linearGradient id="panelFill" x1="0" y1="0" x2="0" y2="1">
        <stop offset="0" stop-color="#2ea0ee"/>
        <stop offset="1" stop-color="#1a7fd4"/>
      </linearGradient>
    </defs>
    <!-- question banner -->
    <path d="M0 158 H470" stroke="var(--blue)" stroke-width="6" fill="none"/>
    <rect x="0" y="168" width="560" height="378" fill="url(#bannerFill)"/>
    <path d="M0 556 H470" stroke="var(--blue)" stroke-width="6" fill="none"/>
    <!-- meaning panel -->
    <rect x="474" y="540" width="10" height="560" fill="var(--orange)"/>
    <rect x="490" y="540" width="316" height="593" fill="url(#panelFill)"/>
    <!-- rings around the photo -->
    <circle cx="626" cy="369" r="252" fill="var(--white)"/>
    <circle cx="626" cy="369" r="262" fill="none" stroke="var(--orange)" stroke-width="14"/>
    <circle cx="626" cy="369" r="208" fill="none" stroke="var(--blue)" stroke-width="10"/>
    <!-- footer band -->
    <path d="M0 1068 H600 Q630 1068 640 1090 L660 1133 H0 Z" fill="var(--orange)"/>
    <path d="M370 1133 L392 1112 H420 L398 1133 Z M420 1133 L442 1112 H470 L448 1133 Z M470 1133 L492 1112 H520 L498 1133 Z" fill="var(--ink)"/>
  </svg>

  <div class="photo" role="img" aria-label="Photo of a businessman drawing a rising bar chart with an upward arrow"></div>

  <div class="brand">
    <span class="brand-dot"></span>
    <span class="brand-name">Tallowcrest Partners</span>
  </div>
  <p class="brand-tag">YOUR WEALTH ADVISORS</p>
  <span class="divider"></span>
  <div class="call">
    <p class="call-line">Simply call or email us</p>
    <p class="call-quote">And quote ‘KORVEN’</p>
  </div>

  <h1 class="headline">ARE YOU WORKING</h1>
  <p class="subline">LONG HOURS AND FEEL LIKE YOU ARE NOT<br>REAPING THE BENEFITS YOU SHOULD BE?</p>
  <ul class="questions">
    <li><span class="q-icon"></span><span>Do you have work life balance?</span></li>
    <li><span class="q-icon"></span><span>Do you understand your business-<br>es strengths and weaknesses?</span></li>
    <li><span class="q-icon"></span><span>Do you feel like you have potential<br>to grow?</span></li>
  </ul>

  <h2 class="pill pill-about">ABOUT US</h2>
  <p class="about-text">Our business is to help you better understand your business and help you to prepare unique strategies to improve the success and value of your business. We can assist to streamline your financial service relationships, providing all financial services under one roof. Such as, accounting and taxation, business planning, wealth planning, smsf, insurance, loan broking, general insurance and business planning.</p>

  <h2 class="pill pill-special">SPECIALISED IN</h2>
  <ul class="special-list">
    <li>By having a review, we guarantee<br>we will provide some financial benefit</li>
    <li>We are offering a cohesive and comprehensive team<br>who will provide many financial services under one roof</li>
    <li>We specialise in business</li>
  </ul>

  <div class="cta">
    <p class="cta-title">HOW TO TAKE ADVANTAGE</p>
    <p class="cta-sub">OF YOUR INITIAL COMPLIMENTARY BUSINESS CHECK</p>
  </div>

  <div class="contact">
    <div class="contact-row">
      <span class="contact-item">
        <svg width="13" height="13" viewBox="0 0 24 24" aria-hidden="true"><path d="M6.6 10.8a15 15 0 0 0 6.6 6.6l2.2-2.2a1 1 0 0 1 1-.25 11.4 11.4 0 0 0 3.6.57 1 1 0 0 1 1 1V20a1 1 0 0 1-1 1A17 17 0 0 1 3 4a1 1 0 0 1 1-1h3.5a1 1 0 0 1 1 1c0 1.25.2 2.45.57 3.6a1 1 0 0 1-.25 1z" fill="#fff"/></svg>
        1300 555 019
      </span>
      <span class="contact-item">
        <svg width="13" height="13" viewBox="0 0 24 24" aria-hidden="true"><circle cx="12" cy="12" r="10" fill="none" stroke="#fff" stroke-width="2"/><path d="M2 12h20M12 2c3 3 3 17 0 20M12 2c-3 3-3 17 0 20" fill="none" stroke="#fff" stroke-width="1.6"/></svg>
        info@tallowcrestpartners.com.au
      </span>
    </div>
    <div class="contact-row">
      <span class="contact-item">
        <svg width="13" height="11" viewBox="0 0 24 18" aria-hidden="true"><rect x="1" y="1" width="22" height="16" rx="2" fill="#fff"/><path d="M2 2l10 8 10-8" fill="none" stroke="#f07d1a" stroke-width="2"/></svg>
        www.tallowcrestpartners.com.au
      </span>
    </div>
  </div>

  <section class="meaning">
    <h2 class="meaning-title">What does this</h2>
    <p class="meaning-sub">mean for you?</p>
    <ul class="meaning-list">
      <li>Coordinated approach and one simple phone call to meet your financial requirements. This saves you time and effort</li>
      <li>A financial services team working together for your business review will ensure you have savings and maximise your financial position with a solid team behind you, all coordinated and on the same team</li>
    </ul>
  </section>
</main>
</body>
</html>
```